Harbor Crest Holdings Corporate Showcase

Provide an attractive Corporate Website for a boutique Investment Company to showcase our activities and corporate interests.

Our Company works across a number of Sectors including

Real Estate
E-Commerce
Healthcare
Beauty & Personal Care
Technology
Resources

Lets keep the personality

Modern
Global
Sophisticated
Calm
Interesting

Lets keep the pages with MINIMAL Words
Lets use Photos/ Imagery to tell the story

We'll need a Banner Menu -
About Us
Expertise
Global Outlook
Sectors
Management
Media
Contact Us

Many thanks
Best wishes
Dennis.

Target Market(s)

Investors
Clients

Coding

Coded - Design and coding required

Number of Pages Required

5+ page

Font styles to use
Sans Serif

Colors
886aae
3176b5
00a990
f68e4d
f04a50
e667a6

Requirements
Must have
• WordPress Coding

Checkout this Website for look and feel - its cool:
www.qvr-example.com

Harbor Crest Partners
(Harbor Crest Holdings LLP)
London
E9 4ZX
United Kingdom

www.HarborCrestPartners-example.com
Nice to have
• Sophisticated colour palette - black/ brown/ blue/ purple/

```html
<!DOCTYPE html>
<html lang="en">
<head>
<meta charset="utf-8">
<title>Harbor Crest Holdings</title>
<link href="https://fonts.googleapis.com/css2?family=Poppins:wght@600;700;800&family=IBM+Plex+Sans:wght@400;500;600&display=swap" rel="stylesheet">
<style>
:root{
  --blue:#2a5ea8;
  --purple:#7b55a6;
  --ink:#1d1d1f;
  --text:#333;
  --footer:#262427;
  --footer-text:#d8d8dc;
  --line:#d9d9d9;
}
*{margin:0;padding:0;box-sizing:border-box}
html,body{width:1200px;height:2988px;overflow:hidden;background:#fff}
body{position:relative;font-family:"IBM Plex Sans",sans-serif;color:var(--text)}
.abs{position:absolute}
.heading{font-family:"Poppins",sans-serif;font-weight:700;color:var(--ink)}
.rule{position:absolute;height:3px;width:50px;background:var(--blue)}
.btn{position:absolute;background:var(--purple);color:#fff;font-family:"Poppins",sans-serif;font-weight:700;display:flex;align-items:center;justify-content:center;text-transform:uppercase}
/* header */
.brand{display:flex;align-items:center;gap:12px;font-weight:600;font-size:23px;color:var(--blue);letter-spacing:.5px}
.brand-mark{width:42px;height:42px;border:2px solid var(--purple);border-radius:50%}
.nav{position:absolute;top:88px;left:128px;width:940px;display:flex;justify-content:space-between;font-size:15px;font-weight:500;color:var(--ink)}
.nav .active{color:var(--purple);text-decoration:underline;text-underline-offset:4px}
.follow{top:37px;left:755px;font-size:10px;font-weight:500;color:var(--ink);display:flex;align-items:center;gap:8px}
.soc{width:26px;height:26px;border-radius:50%;background:var(--blue)}
.soc.dark{background:#1a1a40}
.call{top:26px;left:908px;display:flex;align-items:center;gap:10px}
.call small{display:block;font-size:10px;font-weight:500;color:var(--ink)}
.call b{font-size:17px;font-weight:500;color:var(--ink)}
/* hero */
.hero{top:122px;left:0;width:1200px;height:555px;background:linear-gradient(180deg,#5c6f8a 0%,#7a6252 45%,#4b3a2e 100%)}
.hero-title{top:290px;width:1200px;text-align:center;font-family:"Poppins",sans-serif;font-weight:800;font-size:46px;color:#fff}
.hero-sub{top:349px;width:1200px;text-align:center;font-family:"Poppins",sans-serif;font-weight:600;font-size:19px;color:#fff}
.dots{top:619px;left:556px;display:flex;gap:9px;align-items:center}
.dots i{width:9px;height:9px;border-radius:50%;background:#fff;display:block}
.dots i.on{width:13px;height:13px;border:2px solid #fff;background:var(--purple)}
/* services */
.service{position:absolute;width:210px;text-align:center}
.service h3{font-weight:600;font-size:16px;color:var(--blue);margin-top:12px;letter-spacing:.3px;white-space:nowrap;margin-left:-20px;margin-right:-20px}
.service p{font-size:13.5px;line-height:18.5px;margin-top:10px}
.svc-btn{position:relative;margin:18px auto 0;width:91px;height:27px;font-size:10px;background:var(--purple);color:#fff;font-family:"Poppins",sans-serif;font-weight:700;display:flex;align-items:center;justify-content:center}
/* photos */
.photo{position:absolute}
.connector{position:absolute;height:2px;background:var(--purple)}
.node{position:absolute;width:12px;height:12px;border-radius:50%;background:var(--purple)}
.para{position:absolute;font-size:16.5px;line-height:23.2px;color:var(--text)}
.sectors{position:absolute;top:1718px;left:180px;width:218px;list-style:none}
.sectors li{height:41.7px;display:flex;align-items:center;gap:14px;font-size:16px;color:var(--ink);border-bottom:1px solid var(--line)}
.sectors li:last-child{border-bottom:none}
.sectors li::before{content:"";border-left:5px solid var(--ink);border-top:4px solid transparent;border-bottom:4px solid transparent;margin-left:14px}
/* footer */
.footer{top:2646px;left:0;width:1200px;height:342px;background:var(--footer)}
.f-head{position:absolute;top:2692px;font-family:"Poppins",sans-serif;font-weight:700;font-size:13px;color:#fff}
.f-menu{position:absolute;top:2728px;left:467px;list-style:none;font-size:12px;line-height:20px;color:var(--footer-text)}
.f-item{position:absolute;display:flex;gap:10px;font-size:12px;line-height:16px;color:var(--footer-text)}
.f-icon{width:22px;height:22px;border-radius:50%;background:#fff;flex:none;display:flex;align-items:center;justify-content:center}
.f-rule{top:2918px;left:135px;width:933px;height:1px;background:#444}
.copy{top:2951px;width:1200px;text-align:center;font-size:9.5px;color:var(--footer-text)}
</style>
</head>
<body>

<header>
  <div class="abs brand" style="top:22px;left:128px"><span class="brand-mark"></span>HARBOR CREST</div>
  <div class="abs follow">FOLLOW US <span class="soc"></span><span class="soc dark"></span></div>
  <div class="abs call">
    <svg width="32" height="32" viewBox="0 0 32 32"><circle cx="16" cy="16" r="15" fill="var(--blue)"/><path d="M11 9c1 0 2 3 2 4s-2 1-1 3 3 4 4 4 1-2 3-1 3 1 3 2-2 3-4 3c-5 0-10-6-10-11 0-2 2-4 3-4z" fill="#fff"/></svg>
    <div><small>CALL US</small><b>555.014.2290</b></div>
  </div>
  <nav class="nav">
    <span class="active">HOME</span><span>ABOUT US</span><span>EXPERTISE</span><span>GLOBAL OUTLOOK</span><span>SECTORS</span><span>MANAGEMENT</span><span>MEDIA</span><span>CONTACT US</span>
  </nav>
</header>

<section>
  <div class="abs hero" role="img" aria-label="Upward view of city skyscrapers against a blue sky"></div>
  <h1 class="abs hero-title">BOUTIQUE INVESTMENT</h1>
  <p class="abs hero-sub">LOREM IPSUM IS SIMPLY DUMMY TEXT OF THE PRINTING</p>
  <div class="btn" style="top:395px;left:525px;width:149px;height:46px;font-size:16px">READ MORE</div>
  <div class="abs dots"><i></i><i></i><i class="on"></i><i></i><i></i></div>
</section>

<section>
  <h2 class="abs heading" style="top:718px;width:1200px;text-align:center;font-size:23px">OUR SERVICES</h2>
  <div class="rule" style="top:761px;left:577px"></div>

  <div class="service" style="top:808px;left:175px">
    <svg width="60" height="62" viewBox="0 0 60 62" fill="none" stroke="var(--blue)" stroke-width="2.5"><circle cx="32" cy="14" r="11"/><path d="M32 7v14M35 10h-4a2 2 0 000 4h2a2 2 0 010 4h-4"/><path d="M32 25v10"/><path d="M4 46c6-6 12-6 18-3h10a3 3 0 010 6H22M32 49l16-8a3 3 0 013 5L32 58H16l-8-4"/></svg>
    <h3>INVESTMENT ADVISORY</h3>
    <p>Lorem ipsum dolor sit amet cons ectetur adipiscing eli sed do eiusmod tempor incid.</p>
    <div class="svc-btn">READ MORE</div>
  </div>
  <div class="service" style="top:808px;left:495px">
    <svg width="56" height="62" viewBox="0 0 56 62" fill="none" stroke="var(--blue)" stroke-width="2.5"><rect x="6" y="8" width="26" height="50"/><rect x="32" y="24" width="18" height="34"/><path d="M12 16h5M21 16h5M12 25h5M21 25h5M12 34h5M21 34h5M12 43h5M21 43h5M37 32h8M37 40h8M37 48h8M15 58v-8h8v8"/></svg>
    <h3>ASSET MANAGEMENT</h3>
    <p>Lorem ipsum dolor sit amet cons ectetur adipiscing eli sed do eiusmod tempor incid.</p>
    <div class="svc-btn">READ MORE</div>
  </div>
  <div class="service" style="top:808px;left:811px">
    <svg width="56" height="62" viewBox="0 0 56 62" fill="var(--blue)"><rect x="6" y="44" width="8" height="14"/><rect x="18" y="36" width="8" height="22"/><rect x="30" y="28" width="8" height="30"/><rect x="42" y="20" width="8" height="38"/><path d="M6 36l18-12 8 5 14-11" fill="none" stroke="var(--blue)" stroke-width="3"/><path d="M40 14h10v10z"/></svg>
    <h3>GROWTH CAPITAL</h3>
    <p>Lorem ipsum dolor sit amet cons ectetur adipiscing eli sed do eiusmod tempor incid.</p>
    <div class="svc-btn">READ MORE</div>
  </div>
</section>

<section>
  <div class="connector" style="top:1149px;left:0;width:151px"></div>
  <div class="photo" style="top:1118px;left:151px;width:410px;height:432px;background:linear-gradient(180deg,#3f78d0 0%,#9ab8e0 40%,#d9d4c4 65%,#6d6a63 100%)" role="img" aria-label="Modern two-storey commercial building under a blue sky"></div>
  <div class="node" style="top:1144px;left:145px"></div>
  <p class="abs" style="top:1153px;left:625px;font-size:18px;font-weight:500;color:var(--ink)">WELCOME TO</p>
  <h2 class="abs" style="top:1174px;left:624px;font-weight:600;font-size:40px;color:var(--blue);letter-spacing:.5px">HARBOR CREST</h2>
  <div class="rule" style="top:1229px;left:625px"></div>
  <p class="para" style="top:1260px;left:625px;width:425px">At vero eos et accusamus et iusto odio dignissimos ducimus qui blanditiis praesentium voluptatum deleniti atque corrupti quos dolores et quas molestias excepturi sint occaecati cupiditate non provident, similique sunt in culpa qui officia deserunt mollitia animi, id est laborum et dolorum fuga. Et harum quidem rerum facilis est et expedita distinctio. Nam libero tempore, cum soluta nobis est eligendi optio cumque nihil impedit quo minus</p>
  <div class="btn" style="top:1475px;left:626px;width:112px;height:33px;font-size:13px">READ MORE</div>
</section>

<section>
  <h2 class="abs heading" style="top:1642px;left:172px;font-size:23px">OUR SECTORS</h2>
  <div class="rule" style="top:1685px;left:172px"></div>
  <ul class="sectors">
    <li>Real Estate</li><li>E-Commerce</li><li>Healthcare</li><li>Beauty &amp; Personal Care</li><li>Technology</li><li>Resources</li>
  </ul>
  <div class="btn" style="top:1997px;left:177px;width:111px;height:34px;font-size:13px">READ MORE</div>
  <div class="photo" style="top:1642px;left:627px;width:441px;height:412px;background:linear-gradient(180deg,#1e3a8f 0%,#5b78b8 38%,#8a7a70 62%,#b9a68e 100%)" role="img" aria-label="Glass and stone office block with landscaped forecourt"></div>
  <div class="connector" style="top:1676px;left:1061px;width:139px"></div>
  <div class="node" style="top:1671px;left:1056px"></div>
</section>

<section>
  <div class="connector" style="top:2168px;left:0;width:151px"></div>
  <div class="photo" style="top:2139px;left:151px;width:410px;height:432px;background:linear-gradient(160deg,#1d4fb8 0%,#e8e4de 45%,#d68a68 70%,#2b3550 100%)" role="img" aria-label="Apartment building facade with balconies against a blue sky"></div>
  <div class="node" style="top:2163px;left:145px"></div>
  <h2 class="abs heading" style="top:2184px;left:627px;font-size:23px">LATEST NEWS</h2>
  <div class="rule" style="top:2228px;left:627px"></div>
  <p class="para" style="top:2267px;left:627px;width:425px">At vero eos et accusamus et iusto odio dignissimos ducimus qui blanditiis praesentium voluptatum deleniti atque corrupti quos dolores et quas molestias excepturi sint occaecati cupiditate non provident, similique sunt in culpa qui officia deserunt mollitia animi, id est laborum et dolorum fuga. Et harum quidem rerum facilis est et expedita distinctio. Nam libero tempore, cum soluta nobis est eligendi optio cumque nihil impedit quo minus</p>
  <div class="btn" style="top:2485px;left:630px;width:110px;height:33px;font-size:13px">READ MORE</div>
</section>

<footer>
  <div class="abs footer"></div>
  <div class="abs brand" style="top:2763px;left:128px"><span class="brand-mark"></span>HARBOR CREST</div>

  <h4 class="f-head" style="left:467px">MENU</h4>
  <ul class="f-menu">
    <li>HOME</li><li>ABOUT US</li><li>EXPERTISE</li><li>GLOBAL OUTLOOK</li><li>SECTORS</li><li>MANAGEMENT</li><li>MEDIA</li><li>CONTACT US</li>
  </ul>

  <h4 class="f-head" style="left:683px">CONTACT US</h4>
  <div class="f-item" style="top:2729px;left:683px">
    <span class="f-icon"><svg width="10" height="13" viewBox="0 0 10 13"><path d="M5 0a5 5 0 015 5c0 3-5 8-5 8S0 8 0 5a5 5 0 015-5z" fill="var(--footer)"/><circle cx="5" cy="5" r="2" fill="#fff"/></svg></span>
    <div>2750 Marlow Terrace<br>Westbrook, CA 90412</div>
  </div>
  <div class="f-item" style="top:2781px;left:683px">
    <span class="f-icon"><svg width="12" height="12" viewBox="0 0 12 12"><path d="M2 1c1 0 2 2 2 3s-1 1 0 2 2 2 3 2 1-1 2-1 2 1 2 2-1 2-2 2C5 11 1 7 1 3c0-1 0-2 1-2z" fill="var(--footer)"/></svg></span>
    <div>Call Us<br>555.014.2290</div>
  </div>
  <div class="f-item" style="top:2832px;left:683px">
    <span class="f-icon"><svg width="12" height="9" viewBox="0 0 12 9"><rect width="12" height="9" fill="var(--footer)"/><path d="M0 0l6 5 6-5" fill="none" stroke="#fff"/></svg></span>
    <div>E mail Us<br>info@harborcrest-example.com</div>
  </div>

  <h4 class="f-head" style="left:965px">FOLLOW US</h4>
  <div class="f-item" style="top:2729px;left:965px"><span class="f-icon"></span><div>Like us on<br>BRIGHTWALL</div></div>
  <div class="f-item" style="top:2779px;left:965px"><span class="f-icon"></span><div>Follow us on<br>QUILLSTREAM</div></div>
  <div class="f-item" style="top:2830px;left:965px"><span class="f-icon"></span><div>Follow us on<br>WORKNEST</div></div>

  <div class="abs f-rule"></div>
  <p class="abs copy">Copyright © 2020 All Rights Reserved</p>
</footer>

</body>
</html>
```